Website for Briar Hollow Gathering Church

Wordpress website design required for Briar Hollow Gathering Church. We are a family oriented church catering for age groups from school age to elderly people. The church has a wide variety of activities which it coordinates. The idea is to describe the activities on the activities page, but cross-link them to show which would be applicable to the different age groups.

We would like an inviting website which is easy to read and navigate.

Target Market(s)

Very wide audience - from school age youth to elderly people, so design and style should cater for both audiences.

Industry/Entity Type

Church

Coding

Coded - Design and coding required

Number of Pages Required

5+ page

Font styles to use
Sans Serif

Colors
0255a3
ffffff
0792cd
f78f20

Requirements
Must have
• Inviting website.
• Clear readable font.
• Space to import photos to balance text on each page.
• Need to project a dynamic and progressive feel for the church.
• Easy to navigate.
Nice to have
• Scrolling photos on pages. Ability to enter questions/ comments/prayer requests on Home page.
Should not have
• Conservative audience, so should not be too bold.

```html
<!DOCTYPE html>
<html lang="en">
<head>
<meta charset="utf-8">
<title>Briar Hollow Gathering Church</title>
<link href="https://fonts.googleapis.com/css2?family=Roboto:wght@300;400;500;700&display=swap" rel="stylesheet">
<style>
:root{
  --blue-deep:#0255a3;
  --blue-sky:#0792cd;
  --orange:#f78f20;
  --white:#ffffff;
  --ink:#222222;
  --text:#666666;
  --grey-bg:#f4f4f4;
  --footer:#0b4f9c;
  --footer-dark:#083d7c;
}
*{box-sizing:border-box;margin:0;padding:0}
html,body{width:1200px;height:2719px;overflow:hidden}
body{font-family:'Roboto',Arial,sans-serif;color:var(--ink);background:var(--white);position:relative}
.section{position:absolute;left:0;width:1200px}
.abs{position:absolute}

/* header */
.site-header{top:0;height:112px;background:var(--white)}
.brand{left:100px;top:62px;display:flex;align-items:center;gap:10px;font-size:17px;font-weight:500;color:var(--blue-deep)}
.brand-dot{width:12px;height:12px;border-radius:50%;background:var(--blue-deep)}
.contact-bar{right:94px;top:16px;display:flex;gap:44px;font-size:15px;color:#444}
.contact-bar span{display:flex;align-items:center;gap:12px}
.contact-bar b{font-weight:500;color:#111}
.main-nav{left:408px;top:58px;width:792px;height:54px;background:var(--blue-deep)}
.main-nav ul{list-style:none;display:flex;height:100%;align-items:center}
.main-nav li{color:var(--white);font-size:15px;padding:0 30px}
.main-nav li.active{background:var(--orange);height:100%;display:flex;align-items:center;padding:0 30px 0 54px;clip-path:polygon(30px 0,100% 0,100% 100%,0 100%)}

/* hero */
.hero{top:112px;height:508px;background:linear-gradient(135deg,#4a4038 0%,#2d2722 45%,#5a4d40 100%)}
.hero-title{top:172px;width:100%;text-align:center;color:var(--white);font-size:44px;font-weight:500}
.hero-text{top:238px;left:290px;width:620px;text-align:center;color:var(--white);font-size:17px;line-height:28px}
.hero-btn{top:327px;left:520px;width:160px;height:45px;border:2px solid var(--white);color:var(--white);font-size:14px;display:flex;align-items:center;justify-content:center}
.hero-arrow{top:237px;width:42px;height:42px;border-radius:50%;background:rgba(0,0,0,.55);display:flex;align-items:center;justify-content:center}

/* service times */
.service-band{top:620px;height:91px;background:var(--orange)}
.service-band .frame{position:absolute;inset:5px 4px;border:1px dashed rgba(255,255,255,.8)}
.service{top:19px;color:var(--white)}
.service h3{font-size:17px;font-weight:700;margin-bottom:8px}
.service p{font-size:15px}

/* welcome */
.welcome{top:711px;height:346px;text-align:center}
.section-title{font-size:27px;font-weight:500;color:#111}
.welcome .section-title{position:absolute;top:55px;width:100%}
.welcome-text{top:102px;left:172px;width:856px;font-size:13.5px;line-height:24px;color:var(--text)}
.btn{display:flex;align-items:center;justify-content:center;color:var(--white);font-size:14px;border-radius:3px}
.btn-blue{background:var(--blue-sky);box-shadow:0 3px 0 var(--blue-deep)}
.btn-orange{background:var(--orange);box-shadow:0 3px 0 #c86c0c}

/* about */
.about{top:1057px;height:479px;background:linear-gradient(180deg,var(--blue-sky) 0%,#0a84c6 100%)}
.about .section-title{position:absolute;top:55px;width:100%;text-align:center;color:var(--white)}
.card{top:118px;width:304px;color:var(--white)}
.photo{width:100%}
.card .photo{height:183px}
.card h3{font-size:17px;font-weight:700;margin:32px 0 12px}
.card p{font-size:12.5px;line-height:22px}

/* prayer */
.prayer{top:1536px;height:382px}
.prayer .section-title{position:absolute;left:98px;top:56px;font-size:25px}
.field{border:1px solid #d4d4d4;font-size:12px;color:#aaa;padding:10px 14px;background:var(--white)}
.prayer-photo{left:752px;top:58px;width:350px;height:265px;box-shadow:0 2px 8px rgba(0,0,0,.35);border:3px solid var(--white)}

/* news */
.news{top:1918px;height:479px;background:var(--grey-bg)}
.news .section-title{position:absolute;top:56px;width:100%;text-align:center}
.post{top:125px;width:316px}
.post .photo{height:180px}
.post h3{font-size:15px;font-weight:700;color:#333;margin-top:24px}
.post .meta{font-size:9px;color:#888;margin-top:8px}
.post p{font-size:12px;line-height:21px;color:var(--text);margin-top:12px}

/* footer */
.site-footer{top:2397px;height:268px;background:linear-gradient(180deg,var(--footer) 0%,#0a4a92 100%);color:var(--white)}
.footer-col{top:54px}
.footer-col h4{font-size:18px;font-weight:700;margin-bottom:18px}
.footer-col ul{list-style:none}
.footer-col li{font-size:13.5px;height:34px;display:flex;align-items:center;gap:16px}
.social{display:flex;gap:8px}
.social span{width:36px;height:36px;border:2px solid var(--white);border-radius:50%}
.join-text{font-size:12.5px;line-height:24px;width:200px}
.join-btn{margin-top:14px;width:92px;height:33px;font-size:12px;border-radius:2px;background:var(--orange)}
.copyright{top:2665px;height:54px;background:var(--footer-dark);color:var(--white);font-size:12px;display:flex;align-items:center;justify-content:center}
</style>
</head>
<body>

<header class="section site-header">
  <div class="abs brand"><span class="brand-dot"></span>Briar Hollow Gathering Church</div>
  <div class="abs contact-bar">
    <span>
      <svg width="22" height="22" viewBox="0 0 22 22"><rect width="22" height="22" rx="3" fill="#0792cd"/><path d="M7 5l3 3-1.5 2a8 8 0 0 0 3.5 3.5l2-1.5 3 3-2 2c-5 0-10-5-10-10z" fill="#fff"/></svg>
      Call us on <b>5210 4873</b>
    </span>
    <span>
      <svg width="22" height="22" viewBox="0 0 22 22"><rect width="22" height="22" rx="3" fill="#0792cd"/><rect x="5" y="7" width="12" height="9" fill="#fff"/><path d="M5 7l6 5 6-5" stroke="#0792cd" stroke-width="1.4" fill="none"/></svg>
      Email us on <b>hello@briarhollow.example</b>
    </span>
  </div>
  <nav class="abs main-nav">
    <ul>
      <li class="active">Home</li>
      <li>Age Group</li>
      <li>Activities</li>
      <li>Events Calendar</li>
      <li>About Us</li>
      <li>Contact Us</li>
    </ul>
  </nav>
</header>

<section class="section hero" role="img" aria-label="Photo of church members sharing a meal on an outdoor patio">
  <h1 class="abs hero-title">BRIAR HOLLOW GATHERING CHURCH.</h1>
  <p class="abs hero-text">Our mission is to reflect the love of God as revealed in Jesus and through His Spirit to make him known by word, sign and deed</p>
  <div class="abs hero-btn">READ MORE INFO</div>
  <div class="abs hero-arrow" style="left:78px"><svg width="14" height="14" viewBox="0 0 14 14"><path d="M9 2L4 7l5 5" stroke="#fff" stroke-width="2" fill="none"/></svg></div>
  <div class="abs hero-arrow" style="left:1092px"><svg width="14" height="14" viewBox="0 0 14 14"><path d="M5 2l5 5-5 5" stroke="#fff" stroke-width="2" fill="none"/></svg></div>
</section>

<section class="section service-band">
  <div class="frame"></div>
  <div class="abs service" style="left:96px"><h3>ALDER CROSSING</h3><p>Sundays: 9 a.m., 11:15 a.m., 5 p.m., 7:15 p.m.</p></div>
  <div class="abs service" style="left:453px"><h3>WILLOW BEND |&nbsp; OAKRIDGE</h3><p>Saturdays: 5 p.m., 7:15 p.m. &nbsp;|&nbsp; Sundays: 9 a.m., 11:15 a.m.</p></div>
  <div class="abs service" style="left:887px"><h3>STONEBROOK</h3><p>Sundays: 9 a.m., 11:15 a.m., 5 p.m.</p></div>
</section>

<section class="section welcome">
  <h2 class="section-title">WELCOME TO BRIAR HOLLOW GATHERING CHURCH</h2>
  <p class="abs welcome-text">Since 1958, the Church has had two redevelopment phases and now closely resembles the original 1950s masterplan. Appropriately for the majestic real estate on which it is built, Church stationery and logo depicts 'Hope on the Rise'. Firstly as the Briar Hollow Chapel and from 1977 following the formation of the Gathering Fellowship, as the Briar Hollow Gathering Church, it has been a place of community worship in the Town of Fernvale and for spreading the good news of the gospel of Jesus.</p>
  <div class="abs btn btn-blue" style="left:434px;top:244px;width:157px;height:40px">READ MORE INFO</div>
  <div class="abs btn btn-orange" style="left:607px;top:244px;width:160px;height:40px">OUR MISSION STATE</div>
</section>

<section class="section about">
  <h2 class="section-title">ABOUT BHGC</h2>
  <article class="abs card" style="left:98px">
    <div class="photo" role="img" aria-label="Photo of church members chatting in a garden" style="background:linear-gradient(135deg,#6f8a4a,#b59a78 60%,#8a6a58)"></div>
    <h3>WHO WE ARE</h3>
    <p>We hold two services which are at 8 am (traditional worship service where we sing hymns) and at 10 am (family worship service) where the children</p>
  </article>
  <article class="abs card" style="left:448px">
    <div class="photo" role="img" aria-label="Photo of a group of members gathered outdoors" style="background:linear-gradient(135deg,#a08060,#c8a070 50%,#6d7a45)"></div>
    <h3>WE BELIEVE</h3>
    <p>We hold two services which are at 8 am (traditional worship service where we sing hymns) and at 10 am (family worship service) where the children</p>
  </article>
  <article class="abs card" style="left:798px">
    <div class="photo" role="img" aria-label="Photo of members enjoying tea in the church hall" style="background:linear-gradient(135deg,#b88a80,#e6ddd2 55%,#9a6a60)"></div>
    <h3>WELCOME</h3>
    <p>We hold two services which are at 8 am (traditional worship service where we sing hymns) and at 10 am (family worship service) where the children</p>
  </article>
</section>

<section class="section prayer">
  <h2 class="section-title">PRAYER REQUESTS</h2>
  <div class="abs field" style="left:98px;top:112px;width:295px;height:36px">Name</div>
  <div class="abs field" style="left:419px;top:112px;width:294px;height:36px">Enter Questions</div>
  <div class="abs field" style="left:98px;top:165px;width:615px;height:96px">Name</div>
  <div class="abs btn btn-orange" style="left:98px;top:282px;width:185px;height:40px;font-size:15px">PRAYER REQUESTS</div>
  <div class="abs prayer-photo" role="img" aria-label="Photo of two volunteers serving food" style="background:linear-gradient(135deg,#8a6a50,#c0a888 45%,#5a6a48)"></div>
</section>

<section class="section news">
  <h2 class="section-title">OUR LATEST NEWS</h2>
  <article class="abs post" style="left:105px">
    <div class="photo" role="img" aria-label="Photo of members seated together in a lounge" style="background:linear-gradient(135deg,#7a5a48,#c48aa0 50%,#3a2e2a)"></div>
    <h3>CURABITUR LOBORTIS</h3>
    <div class="meta">AUGUST 2, 2016 &nbsp;|&nbsp; 1 COMMENT(S)</div>
    <p>It is a long established fact that a reader will be distracted by the readable content of a page when looking...</p>
  </article>
  <article class="abs post" style="left:450px">
    <div class="photo" role="img" aria-label="Photo of members at a gathering in the hall" style="background:linear-gradient(135deg,#6a5040,#d2c0b0 50%,#8a9a50)"></div>
    <h3>CURABITUR LOBORTIS</h3>
    <div class="meta">AUGUST 2, 2016 &nbsp;|&nbsp; 1 COMMENT(S)</div>
    <p>It is a long established fact that a reader will be distracted by the readable content of a page when looking...</p>
  </article>
  <article class="abs post" style="left:792px">
    <div class="photo" role="img" aria-label="Photo of a morning tea in the community room" style="background:linear-gradient(135deg,#7a3a30,#c8a890 50%,#c070a0)"></div>
    <h3>CURABITUR LOBORTIS</h3>
    <div class="meta">AUGUST 2, 2016 &nbsp;|&nbsp; 1 COMMENT(S)</div>
    <p>It is a long established fact that a reader will be distracted by the readable content of a page when looking...</p>
  </article>
</section>

<footer class="section site-footer">
  <div class="abs footer-col" style="left:98px">
    <h4>GET IN TOUCH</h4>
    <ul>
      <li><svg width="12" height="12" viewBox="0 0 12 12"><path d="M2 1l3 3-1 1.5a6 6 0 0 0 2.5 2.5L8 7l3 3-1.5 1.5C5 11.5 .5 7 .5 2.5z" fill="#fff"/></svg>Phone: 5287 1046</li>
      <li><svg width="12" height="12" viewBox="0 0 12 12"><rect x="1" y="4" width="10" height="7" fill="#fff"/><rect x="3" y="1" width="6" height="3" fill="#fff"/></svg>Fax: 03 518 2267</li>
      <li><svg width="12" height="12" viewBox="0 0 12 12"><rect x="1" y="2.5" width="10" height="7" fill="none" stroke="#fff" stroke-width="1.3"/><path d="M1 3l5 4 5-4" stroke="#fff" stroke-width="1.2" fill="none"/></svg>Email: office@briarhollow.example</li>
      <li><svg width="12" height="12" viewBox="0 0 12 12"><circle cx="6" cy="6" r="5" fill="#fff"/></svg>Web: www.briarhollow.example</li>
    </ul>
  </div>
  <div class="abs footer-col" style="left:392px">
    <h4>QUICK LINKS</h4>
    <ul>
      <li><svg width="10" height="10" viewBox="0 0 10 10"><path d="M1 2l3 3-3 3M5 2l3 3-3 3" stroke="#fff" stroke-width="1.3" fill="none"/></svg>About Us</li>
      <li><svg width="10" height="10" viewBox="0 0 10 10"><path d="M1 2l3 3-3 3M5 2l3 3-3 3" stroke="#fff" stroke-width="1.3" fill="none"/></svg>Services</li>
      <li><svg width="10" height="10" viewBox="0 0 10 10"><path d="M1 2l3 3-3 3M5 2l3 3-3 3" stroke="#fff" stroke-width="1.3" fill="none"/></svg>Testimonial</li>
      <li><svg width="10" height="10" viewBox="0 0 10 10"><path d="M1 2l3 3-3 3M5 2l3 3-3 3" stroke="#fff" stroke-width="1.3" fill="none"/></svg>News &amp; Media</li>
    </ul>
  </div>
  <div class="abs footer-col" style="left:616px">
    <h4>SOCIAL MEDIA</h4>
    <div class="social"><span></span><span></span><span></span><span></span><span></span></div>
  </div>
  <div class="abs footer-col" style="left:915px">
    <h4>JOIN US</h4>
    <p class="join-text">Holy Communion is generally held on the 3rd Sunday of the month.</p>
    <div class="btn join-btn">Join Us Now</div>
  </div>
</footer>
<div class="section copyright">Copyrights@2016Company Name , All rights Reserved</div>

</body>
</html>
```